Business Card Design

New business card design

Target Market(s)

Residential & Commercial Property Managers

Industry/Entity Type

Plumbing Services

Contact Information for Business Card

Name - Rowan Keddle, title - Director, Phone Number - 0431 286 517, email - rowan@tbk-plumbing.com.au, Company ABN - 73 215 904 386,

Font styles to use
Sans Serif

Colors
0054AA
0677BA
7BADD7
CADEEF
E8F1F8

```html
<!DOCTYPE html>
<html lang="en">
<head>
<meta charset="utf-8">
<title>TBK Plumbing Services – Business Card</title>
<link rel="stylesheet" href="https://fonts.googleapis.com/css2?family=Montserrat:wght@400;500;700&display=swap">
<style>
  :root {
    --stage: #232323;
    --paper: #ffffff;
    --ink: #1d2229;
    --brand-blue: #2aa8e0;
  }
  * { box-sizing: border-box; margin: 0; padding: 0; }
  html, body { width: 1200px; height: 780px; overflow: hidden; }
  body {
    background: var(--stage);
    font-family: "Montserrat", Arial, sans-serif;
    display: flex;
    align-items: center;
    justify-content: center;
    gap: 30px;
  }
  .card {
    position: relative;
    width: 560px;
    height: 320px;
    background: var(--paper);
    border-radius: 20px;
    border-bottom: 4px solid var(--brand-blue);
    overflow: hidden;
    box-shadow: 0 14px 30px rgba(0,0,0,0.45);
  }
  /* Front */
  .card-front { display: flex; align-items: center; justify-content: center; }
  .wordmark {
    display: flex;
    align-items: center;
    gap: 12px;
    color: var(--ink);
    font-weight: 500;
    font-size: 30px;
    letter-spacing: 0.02em;
  }
  .wordmark-dot {
    width: 16px; height: 16px;
    border-radius: 50%;
    background: var(--brand-blue);
  }
  .card-back .wordmark {
    position: absolute;
    top: 34px;
    right: 30px;
    font-size: 20px;
    gap: 9px;
  }
  .card-back .wordmark-dot { width: 11px; height: 11px; }
  /* Back */
  .info-band {
    position: absolute;
    left: 0; right: 0; bottom: 0;
    height: 136px;
    background: var(--ink);
  }
  .info-rule {
    position: absolute;
    left: 0; right: 0;
    bottom: 142px;
    height: 8px;
    background: var(--brand-blue);
  }
  .name-tag {
    position: absolute;
    top: 96px;
    left: 0;
    padding-left: 30px;
  }
  .name-tag::before {
    content: "";
    position: absolute;
    left: 0; top: 4px;
    width: 12px; height: 58px;
    background: var(--brand-blue);
  }
  .person-name {
    color: var(--brand-blue);
    font-weight: 700;
    font-size: 28px;
    line-height: 1.1;
  }
  .person-title {
    color: var(--ink);
    font-size: 16px;
    margin-top: 4px;
    padding-left: 14px;
  }
  .contact {
    position: absolute;
    left: 150px;
    top: 200px;
    color: var(--paper);
    font-size: 15px;
    line-height: 1.35;
  }
  .abn { margin-bottom: 10px; }
  .contact-line { display: flex; align-items: center; gap: 8px; }
  .contact-line svg { width: 15px; height: 15px; flex: none; }
</style>
</head>
<body>

<section class="card card-front">
  <div class="wordmark"><span class="wordmark-dot"></span>TBK Plumbing Services</div>
</section>

<section class="card card-back">
  <div class="info-rule"></div>
  <div class="info-band"></div>

  <div class="wordmark"><span class="wordmark-dot"></span>TBK Plumbing Services</div>

  <div class="name-tag">
    <p class="person-name">Rowan Keddle</p>
    <p class="person-title">Director</p>
  </div>

  <div class="contact">
    <p class="abn">Company ABN<br>- 73 215 904 386</p>
    <p class="contact-line">
      <svg viewBox="0 0 24 24" aria-hidden="true"><path fill="var(--brand-blue)" d="M6.6 10.8a15 15 0 0 0 6.6 6.6l2.2-2.2c.3-.3.7-.4 1-.2 1.1.4 2.300.6 3.6.6.6 0 1 .4 1 1V20c0 .6-.4 1-1 1A17 17 0 0 1 3 4c0-.6.4-1 1-1h3.5c.6 0 1 .4 1 1 0 1.3.2 2.5.6 3.6.1.3 0 .7-.2 1z"/></svg>
      0431 286 517
    </p>
    <p class="contact-line">
      <svg viewBox="0 0 24 24" aria-hidden="true"><path fill="var(--brand-blue)" d="M3 5h18a1 1 0 0 1 1 1v12a1 1 0 0 1-1 1H3a1 1 0 0 1-1-1V6a1 1 0 0 1 1-1zm9 7.5L20 7H4z"/></svg>
      rowan@tbk-plumbing.com.au
    </p>
  </div>
</section>

</body>
</html>
```